Packaging Design: Logo/Bottle Design for New Botanical Cocktail Brand

We are a new start up, looking to create a new line of Ready to drink Cocktails. The brand name is Verdance Garden Spritzers, infused with fruit, herb, and floral botanicals grown on our farm in New Hampshire. Flavors will include: Herb flavored with cilantro, Berry- flavored with Ridgeglow Berry, Citrus flavored with lemon Verbena & lemon balm, Pear flavored with Quillon pear, Cucumber & Mint. We need a logo and a label design. There are 2 possible bottles to choose from.

Designer has complete freedom with everything! From fonts and colors to bottle caps and closures. Please view the pinterest link for inspirational bottle designs. https://www.pinboardia.com/dellacravitz/garden-spritzers/

Reason: I am extending the deadline for my project to allow more designers to submit their designs.

Target Market(s)

Female 21 to 48 years old. College educated and professional. The type of person that has a passion for a cause and eats and shops local. People that respect an artisan quality product, hand made by a master craftsman.

Industry/Entity Type

Floral

Requirements
Must have
• Clear Bottle, see options attached. You may also choose your own BUT WE MUST SEE THE LOGO AND IMAGERY ON A BOTTLE
• Logo Design: "Verdance Garden Spritzers"
• Label: We can have front and back, or one continuous label. We are open to painted designs.
• The label must contain the following text in quotes:
• Product Name: " Verdance Garden Spritzers "
• "15% Alc. by Vol. (30 proof)"
• "750 mL"
• "Handcrafted and Bottled by Hollowmere Stillbrook Farm and Distillery
• Brambleford, Ashvale-USA"
• The following Text must be in all caps and 3mm in height:
• "Government Warning: (1) According to the Surgeon General, women should not drink alcoholic beverages during pregnancy because of the risk of birth defects. (2) Consumption of alcoholic beverages impairs your ability to drive a car or operate machinery and may cause health problems."
• Must be a space for a bar code: .75 in height by 1.25 in length.
• “www.hollowmerestillbrook.com”
• Must Have the following Statement:
• Infused with fruit, herb, and floral botanicals and sweetened with stevia. Serve cold over ice.
Nice to have
• Antique or vintage botanical illustrations
• https://www.pinboardia.com/dellacravitz/garden-spritzers/
• check out the board for inspiration.
• Think artisanal small batch spirits that are ready to drink out of the bottle. Refreshing flavors just pour over ice and add herb leaves.
• You can use images by doing a search here.
• http://archv.plantrec.example.org/archv/search.xhtml?start=0&collectionFacet=Orchard+Painted+Plate+Archive

```html
<!DOCTYPE html>
<html lang="en">
<head>
<meta charset="utf-8">
<title>Verdance Garden Spritzers – Label</title>
<link rel="stylesheet" href="https://fonts.googleapis.com/css2?family=Montserrat:wght@300;400;700&family=Roboto+Condensed:wght@700&display=swap">
<style>
  :root {
    --canvas-bg: #ecebea;
    --label-white: #ffffff;
    --blush-top: #fbe3e8;
    --blush-mid: #f3b8c6;
    --rose-deep: #d9577f;
    --berry-red: #c9393f;
    --brand-ink: #1c1c1c;
    --mark-red: #c4162f;
    --leaf-green: #2f9a3c;
    --text-white: #ffffff;
    --url-ink: #8a1f3c;
  }
  * { margin: 0; padding: 0; box-sizing: border-box; }
  html, body { width: 844px; height: 1200px; overflow: hidden; }
  body {
    background: var(--canvas-bg);
    font-family: "Montserrat", Arial, sans-serif;
    position: relative;
  }
  .label {
    position: absolute;
    left: 112px; top: 48px;
    width: 620px; height: 1104px;
    background: var(--label-white);
    border-radius: 14px;
    overflow: hidden;
  }
  .brand {
    position: absolute;
    left: 0; top: 40px; width: 100%;
    text-align: center;
    color: var(--brand-ink);
  }
  .brand-dot {
    width: 64px; height: 64px;
    border-radius: 50%;
    background: var(--mark-red);
    margin: 0 auto 60px;
  }
  .brand-name { font-size: 62px; font-weight: 700; line-height: 1; letter-spacing: 1px; }
  .brand-line { font-size: 54px; font-weight: 300; line-height: 1.08; letter-spacing: 2px; }
  .brand-line:first-of-type { margin-top: 6px; }
  .field {
    position: absolute;
    left: 0; top: 430px; width: 100%; height: 600px;
    background: linear-gradient(180deg, var(--label-white) 0%, var(--blush-top) 12%, var(--blush-mid) 45%, var(--rose-deep) 100%);
  }
  .flavor-band {
    position: absolute;
    left: 0; top: 594px; width: 100%; height: 90px;
    background: var(--berry-red);
  }
  .flavor-art {
    position: absolute;
    left: 30px; top: 500px; width: 260px; height: 420px;
    border-radius: 45% 55% 50% 50%;
    background: radial-gradient(ellipse at 45% 30%, #e23a3a 0%, #d4485f 35%, #e27b9a 65%, rgba(226,123,154,0) 100%);
  }
  .details {
    position: absolute;
    left: 300px; top: 700px; width: 295px;
    color: var(--text-white);
    font-size: 17px;
    line-height: 1.3;
  }
  .details p + p { margin-top: 22px; }
  .details .specs { padding-left: 18px; }
  .website {
    position: absolute;
    left: 0; top: 980px; width: 100%;
    text-align: center;
    color: var(--url-ink);
    font-size: 19px;
  }
  .warning {
    position: absolute;
    left: 0; top: 1030px; width: 100%; height: 74px;
    background: var(--leaf-green);
    color: var(--text-white);
    font-family: "Roboto Condensed", Arial, sans-serif;
    font-weight: 700;
    font-size: 13.4px;
    line-height: 1.12;
    text-transform: uppercase;
    text-align: justify;
    padding: 5px 12px;
  }
</style>
</head>
<body>
  <main class="label">
    <header class="brand">
      <div class="brand-dot"></div>
      <div class="brand-name">VERDANCE</div>
      <div class="brand-line">GARDEN</div>
      <div class="brand-line">SPRITZERS</div>
    </header>

    <div class="field"></div>
    <div class="flavor-band"></div>
    <div class="flavor-art" role="img" aria-label="Watercolour illustration of ripe red berries with green leaves over a splash of pink and purple petals"></div>

    <section class="details">
      <p class="specs">Verdance Garden Spritzers”<br>
      • “15% Alc. by Vol. (30 proof)”<br>
      • “750 mL”<br>
      • “Handcrafted and Bottled by Hollowmere Stillbrook Farm and Distillery, Brambleford, Ashvale-USA”</p>
      <p>• Infused with fruit, herb, and floral botanicals and sweetened with stevia. Serve cold over ice.</p>
    </section>

    <p class="website">“www.hollowmerestillbrook.com”</p>

    <footer class="warning">Government warning: (1) According to the Surgeon General, women should not drink alcoholic beverages during pregnancy because of the risk of birth defects. (2) Consumption of alcoholic beverages impairs your ability to drive a car or operate machinery and may cause health problems.</footer>
  </main>
</body>
</html>
```